Stationary Set Rebrand for Brennick

We are a Canadian Distribution and Service Company that was established in 1969. Over the past 5 decades we have expanded our business and have warehouses across Canada. We specialize in adhesive tapes, adhesives, films, safety, warehouse, shipping, janitorial and packaging supplies.

We have updated our logo design and would like a new corporate branding identity that includes a new fresh Stationary Set (Business Cards, Letterhead, Letterhead MS Word, Envelope, Presentation Folders, Email Signatures, Notepad Covers, etc.)

Target Market(s)

Industrial Business Sector

Font styles to use
Sans Serif

Colors
0054AA
0677BA
7BADD7
CADEEF
E8F1F8
0094D4
00A9DD
6FCCEA
C7EBF8
E9F6FB
00AB8E
00BBA5
67D7C9
C6EFE9
E9F9F6
EB3D1F
EC4F4E
F09395
F8D3D4
FCEDEE

Requirements
Should not have
• Colors not too light, darker colours preferred

```html
<!DOCTYPE html>
<html lang="en">
<head>
<meta charset="utf-8">
<title>Brennick Stationery Set</title>
<link href="https://fonts.googleapis.com/css2?family=Roboto:wght@300;400;500;900&display=swap" rel="stylesheet">
<style>
  :root{
    --backdrop:#3b3b3d;
    --ink:#231f20;
    --red:#d71f26;
    --paper:#f6f2f3;
    --white:#ffffff;
    --text:#3d3a3b;
    --muted:#6b6768;
    --blush:#f3dfe0;
    --rule:#c9c6c7;
  }
  *{box-sizing:border-box;margin:0;padding:0}
  html,body{width:1200px;height:933px;overflow:hidden}
  body{background:var(--backdrop);font-family:"Roboto",sans-serif;color:var(--text);position:relative}
  .piece{position:absolute;box-shadow:0 3px 10px rgba(0,0,0,.35)}
  .wordmark{font-family:"Roboto",sans-serif;font-weight:900;color:var(--ink);display:inline-flex;align-items:center;gap:.2em;letter-spacing:-.01em;line-height:1;white-space:nowrap}
  .wordmark::after{content:"";width:.26em;height:.26em;background:var(--red);display:inline-block}
  .wordmark.on-dark{color:var(--white)}
  .red-bar{position:absolute;background:var(--red)}
  .contact{list-style:none;font-size:5.3px;line-height:6.3px;color:var(--text);letter-spacing:.02em}
  .contact li{display:flex;align-items:center;gap:3px}
  .contact.right li{justify-content:flex-end}
  .contact svg{width:4px;height:4px;flex:none}
  .address{font-size:5.3px;line-height:6.3px;letter-spacing:.02em;color:var(--text)}
  .faint-mark{position:absolute;border-radius:50%;background:var(--blush);opacity:.75}

  /* business cards */
  .card-front{left:38px;top:102px;width:219px;height:124px;background:var(--white);border-radius:6px}
  .card-front .wordmark{position:absolute;left:12px;top:14px;font-size:18px}
  .card-front .address{position:absolute;left:12px;top:66px}
  .card-front .contact{position:absolute;left:12px;top:85px}
  .card-front .holder{position:absolute;right:12px;top:76px;text-align:right}
  .holder .name{font-weight:900;color:var(--red);font-size:8px;letter-spacing:.04em}
  .holder .role{font-size:5px;color:var(--muted)}
  .card-front .red-bar{right:0;top:76px;width:5px;height:15px}
  .card-back{left:34px;top:275px;width:223px;height:127px;background:var(--ink);border-radius:5px;display:flex;align-items:center;justify-content:center}
  .card-back .wordmark{font-size:28px}

  /* letterhead */
  .letterhead{left:280px;top:44px;width:306px;height:432px;background:var(--paper)}
  .letterhead .red-bar{right:0;top:0;width:9px;height:100%}
  .letterhead .wordmark{position:absolute;right:29px;top:28px;font-size:18px}
  .letterhead .faint-mark{left:70px;top:170px;width:140px;height:140px}
  .letter{position:absolute;left:31px;top:106px;width:246px}
  .letter .salutation{font-size:8.5px;color:var(--text);margin-bottom:14px}
  .letter p{font-size:4.6px;line-height:7.3px;text-align:justify;color:var(--muted);margin-bottom:7px}
  .letter .closing{font-size:5px;margin-top:11px;color:var(--muted)}
  .letter .signer{margin-top:31px;padding-left:2px;font-size:7px;color:var(--text)}
  .letter .signer-role{padding-left:2px;font-size:5px;color:var(--muted)}
  .letterhead .address,.letterhead .contact{position:absolute;right:29px;text-align:right}
  .letterhead .address{top:367px}
  .letterhead .contact{top:383px}

  /* envelopes */
  .envelope-slip{left:632px;top:80px;width:312px;height:85px;background:var(--paper)}
  .envelope-slip .red-bar{right:0;top:0;width:8px;height:100%}
  .envelope-slip .wordmark{position:absolute;left:19px;top:30px;font-size:19px}
  .envelope-slip .address,.envelope-slip .contact{position:absolute;right:19px;text-align:right}
  .envelope-slip .address{top:22px}
  .envelope-slip .contact{top:38px}
  .envelope-back{left:632px;top:198px;width:343px;height:157px;background:var(--paper)}
  .envelope-back svg.flap{position:absolute;left:0;top:0}
  .envelope-back .wordmark{position:absolute;left:50%;top:16px;transform:translateX(-50%);font-size:22px}
  .envelope-front{left:613px;top:301px;width:345px;height:157px;background:var(--paper)}
  .envelope-front .red-bar{left:0;top:0;width:9px;height:100%}
  .envelope-front .wordmark{position:absolute;left:18px;top:19px;font-size:18px}
  .envelope-front .faint-mark{left:210px;top:22px;width:124px;height:124px}
  .envelope-front .address{position:absolute;left:18px;top:100px}
  .envelope-front .contact{position:absolute;left:18px;top:115px}

  /* notepads */
  .notepad{width:129px;height:188px}
  .notepad .spiral{position:absolute;left:6px;right:6px;top:-7px;height:11px;background:repeating-linear-gradient(90deg,#bdbdbd 0 1.3px,transparent 1.3px 6.4px)}
  .notepad .wordmark{position:absolute;left:50%;transform:translateX(-50%)}
  .notepad .site{position:absolute;left:0;right:0;text-align:center;font-size:5px}
  .notepad-dark{left:1023px;top:77px;background:var(--ink)}
  .notepad-dark .wordmark{top:84px;font-size:18px}
  .notepad-dark .site{top:170px;color:var(--white)}
  .notepad-light{left:1025px;top:297px;background:var(--paper)}
  .notepad-light .wordmark{top:20px;font-size:12px}
  .notepad-light .faint-mark{left:22px;top:62px;width:84px;height:84px}
  .notepad-light .lines{position:absolute;left:13px;right:11px;top:55px;height:106px;background:repeating-linear-gradient(180deg,transparent 0 9.6px,var(--rule) 9.6px 10.1px)}
  .notepad-light .site{top:174px;color:var(--text)}

  /* folder outside */
  .folder-outside{left:47px;top:560px;width:510px;height:321px;background:var(--white);display:flex}
  .folder-outside .back-cover{width:254px;height:100%;background:var(--ink);position:relative}
  .back-cover .wordmark{position:absolute;left:50%;top:150px;transform:translateX(-50%);font-size:36px}
  .back-cover .address{position:absolute;left:0;right:0;top:250px;text-align:center;color:var(--white)}
  .back-cover .divider{position:absolute;left:112px;width:29px;top:269px;border-top:.6px solid var(--white)}
  .back-cover .contact{position:absolute;left:0;right:0;top:276px;color:var(--white);display:grid;grid-template-columns:auto auto;justify-content:center;column-gap:6px}
  .folder-outside .front-cover{flex:1;position:relative}
  .front-cover .wordmark{position:absolute;left:calc(50% - 4px);top:148px;transform:translateX(-50%);font-size:42px}
  .front-cover .red-bar{right:0;top:0;width:9px;height:100%}

  /* folder inside */
  .folder-inside{left:610px;top:562px;width:510px;height:322px;background:linear-gradient(90deg,#ffffff 0%,#f1f1f1 38%,#cfcfcf 50%,#f1f1f1 62%,#ffffff 100%)}
  .folder-inside svg{position:absolute;left:0;top:0}
  .folder-inside .wordmark{position:absolute;top:245px;font-size:34px}
  .folder-inside .pocket-left{left:60px}
  .folder-inside .pocket-right{left:324px}
</style>
</head>
<body>
<svg width="0" height="0" style="position:absolute" aria-hidden="true">
  <defs>
    <symbol id="icon-phone" viewBox="0 0 10 10"><path d="M2 1l2 2-1 1.2c.6 1.3 1.5 2.2 2.8 2.8L7 6l2 2-1.3 1.3C4.5 9 1 5.5.7 2.3z" fill="#d71f26"/></symbol>
    <symbol id="icon-mobile" viewBox="0 0 10 10"><rect x="2.5" y="0.5" width="5" height="9" rx="1" fill="none" stroke="#d71f26" stroke-width="1.2"/></symbol>
    <symbol id="icon-mail" viewBox="0 0 10 10"><rect x="0.5" y="2" width="9" height="6" fill="#d71f26"/><path d="M.5 2L5 5.5 9.5 2" fill="none" stroke="#fff" stroke-width=".8"/></symbol>
    <symbol id="icon-globe" viewBox="0 0 10 10"><circle cx="5" cy="5" r="4.5" fill="#d71f26"/><path d="M.5 5h9M5 .5c2 2.5 2 6.5 0 9M5 .5c-2 2.5-2 6.5 0 9" fill="none" stroke="#fff" stroke-width=".7"/></symbol>
  </defs>
</svg>

<!-- Business card, front -->
<section class="piece card-front">
  <span class="wordmark">Brennick</span>
  <p class="address">412 Cedarfield Road<br>Thunder Bay, Canada 54120</p>
  <ul class="contact">
    <li><svg><use href="#icon-phone"/></svg>807-555-0142</li>
    <li><svg><use href="#icon-mobile"/></svg>807-555-0187</li>
    <li><svg><use href="#icon-mail"/></svg>info@brennick.com</li>
    <li><svg><use href="#icon-globe"/></svg>www.brennick.com</li>
  </ul>
  <div class="holder"><div class="name">DANA WHITLOCK</div><div class="role">President</div></div>
  <span class="red-bar"></span>
</section>

<!-- Business card, back -->
<section class="piece card-back"><span class="wordmark on-dark">Brennick</span></section>

<!-- Letterhead -->
<section class="piece letterhead">
  <span class="faint-mark"></span>
  <span class="wordmark">Brennick</span>
  <div class="letter">
    <p class="salutation">Dear Mr. Harlow,</p>
    <p>Thank you for meeting with our team last week. We have reviewed your warehouse needs and prepared a supply plan covering tapes, films, stretch wrap and shipping cartons. Pricing is attached for your review and our account manager will follow up shortly.</p>
    <p>Our distribution centres across Canada keep core items in stock, so most orders ship the same business day. We can also set up scheduled deliveries for janitorial and safety supplies to keep your site running without interruption.</p>
    <p>Should you need samples before placing an order, simply reply to this letter or call our office. We are glad to arrange a product trial at your facility and to walk your staff through the best options for each application on the line.</p>
    <p>We look forward to working with you and supporting your packaging operations for many years to come.</p>
    <p class="closing">Sincerely,</p>
    <p class="signer">Dana Whitlock</p>
    <p class="signer-role">CEO/ Founder</p>
  </div>
  <p class="address">412 Cedarfield Road<br>Thunder Bay, Canada 54120</p>
  <ul class="contact right">
    <li>807-555-0142<svg><use href="#icon-phone"/></svg></li>
    <li>807-555-0187<svg><use href="#icon-mobile"/></svg></li>
    <li>info@brennick.com<svg><use href="#icon-mail"/></svg></li>
    <li>www.brennick.com<svg><use href="#icon-globe"/></svg></li>
  </ul>
  <span class="red-bar"></span>
</section>

<!-- Envelope, slim -->
<section class="piece envelope-slip">
  <span class="wordmark">Brennick</span>
  <p class="address">412 Cedarfield Road<br>Thunder Bay, Canada 54120</p>
  <ul class="contact right">
    <li>807-555-0142<svg><use href="#icon-phone"/></svg></li>
    <li>807-555-0187<svg><use href="#icon-mobile"/></svg></li>
    <li>info@brennick.com<svg><use href="#icon-mail"/></svg></li>
    <li>www.brennick.com<svg><use href="#icon-globe"/></svg></li>
  </ul>
  <span class="red-bar"></span>
</section>

<!-- Envelope, back with flap -->
<section class="piece envelope-back">
  <svg class="flap" width="343" height="58" viewBox="0 0 343 58"><path d="M0 0H343L335 40Q332 58 314 58H29Q11 58 8 40Z" fill="#231f20"/></svg>
  <span class="wordmark on-dark">Brennick</span>
</section>

<!-- Envelope, front -->
<section class="piece envelope-front">
  <span class="red-bar"></span>
  <span class="faint-mark"></span>
  <span class="wordmark">Brennick</span>
  <p class="address">412 Cedarfield Road<br>Thunder Bay, Canada 54120</p>
  <ul class="contact">
    <li><svg><use href="#icon-phone"/></svg>807-555-0142</li>
    <li><svg><use href="#icon-mobile"/></svg>807-555-0187</li>
    <li><svg><use href="#icon-mail"/></svg>info@brennick.com</li>
    <li><svg><use href="#icon-globe"/></svg>www.brennick.com</li>
  </ul>
</section>

<!-- Notepad cover -->
<section class="piece notepad notepad-dark">
  <span class="spiral"></span>
  <span class="wordmark on-dark">Brennick</span>
  <p class="site">www.brennick.com</p>
</section>

<!-- Notepad page -->
<section class="piece notepad notepad-light">
  <span class="spiral"></span>
  <span class="wordmark">Brennick</span>
  <span class="faint-mark"></span>
  <span class="lines"></span>
  <p class="site">www.brennick.com</p>
</section>

<!-- Presentation folder, outside -->
<section class="piece folder-outside">
  <div class="back-cover">
    <span class="wordmark on-dark">Brennick</span>
    <p class="address">412 Cedarfield Road<br>Thunder Bay, Canada 54120</p>
    <span class="divider"></span>
    <ul class="contact">
      <li><svg><use href="#icon-phone"/></svg>807-555-0142</li>
      <li><svg><use href="#icon-mobile"/></svg>807-555-0187</li>
      <li><svg><use href="#icon-mail"/></svg>info@brennick.com</li>
      <li><svg><use href="#icon-globe"/></svg>www.brennick.com</li>
    </ul>
  </div>
  <div class="front-cover">
    <span class="wordmark">Brennick</span>
    <span class="red-bar"></span>
  </div>
</section>

<!-- Presentation folder, inside -->
<section class="piece folder-inside">
  <svg width="510" height="322" viewBox="0 0 510 322">
    <path d="M0 192H222Q236 192 238 206L255 318V322H0Z" fill="#231f20"/>
    <path d="M510 192H288Q274 192 272 206L255 318V322H510Z" fill="#231f20"/>
  </svg>
  <span class="wordmark on-dark pocket-left">Brennick</span>
  <span class="wordmark on-dark pocket-right">Brennick</span>
</section>
</body>
</html>
```